business card - Helicopter Flight Services, Flight School, etc.

We need a business card design for a new helicopter service.

We offer Helicopter Flight Services, Aerial Filming & Photography, Flight School, and Helicopter Tours. In that order.

Summit BladeAir, Inc.
Dennis Tollerby
SummitBladeair@Kestmail.com
626-418-7352

Based at the Brenwick Airport in Van Nuys, CA. The final design should communicate integrity and safety. Pictures or logos at your discretion.

Card back side - surprise me.

```html
<!DOCTYPE html>
<html lang="en">
<head>
<meta charset="utf-8">
<title>Summit BladeAir, Inc. — Business Card</title>
<link rel="stylesheet" href="https://fonts.googleapis.com/css2?family=Open+Sans:wght@400;600;700&display=swap">
<style>
  :root {
    --backdrop: #e9ebee;
    --card-white: #ffffff;
    --blue-deep: #0c5db0;
    --blue-mid: #1f7fd0;
    --blue-light: #3aa6e6;
    --blue-ink: #1b6fc1;
    --green: #7cc242;
    --shadow: rgba(20, 40, 70, 0.18);
  }
  * { box-sizing: border-box; margin: 0; padding: 0; }
  html, body { width: 1200px; height: 913px; overflow: hidden; }
  body {
    background: var(--backdrop);
    font-family: "Open Sans", Arial, sans-serif;
    position: relative;
  }
  .card {
    position: absolute;
    width: 640px;
    height: 366px;
    background: var(--card-white);
    box-shadow: 0 10px 30px var(--shadow);
    overflow: hidden;
  }

  /* Front */
  .card--front { left: 70px; top: 70px; }
  .front-band {
    position: absolute;
    left: 0; top: 150px;
    width: 240px; height: 216px;
    background: linear-gradient(160deg, var(--blue-light) 0%, var(--blue-mid) 45%, var(--blue-deep) 100%);
  }
  .front-band::before {
    content: "";
    position: absolute;
    left: 0; top: -110px;
    width: 240px; height: 110px;
    background: linear-gradient(160deg, var(--blue-light), var(--blue-mid));
    clip-path: polygon(30% 100%, 100% 0, 100% 100%);
  }
  .brand {
    position: absolute;
    left: 262px; top: 76px;
    display: flex; align-items: center; gap: 12px;
    border-left: 2px solid var(--blue-ink);
    padding: 6px 0 6px 14px;
    white-space: nowrap;
  }
  .brand__mark {
    width: 22px; height: 22px;
    border-radius: 50%;
    background: var(--green);
    flex: none;
  }
  .brand__name {
    font-weight: 700;
    color: var(--blue-ink);
    font-size: 26px;
    line-height: 1.1;
    letter-spacing: 0.3px;
  }
  .contact {
    position: absolute;
    left: 262px; top: 200px;
  }
  .contact__name {
    font-weight: 700;
    font-size: 22px;
    color: var(--blue-ink);
  }
  .contact__role {
    font-size: 14px;
    color: var(--green);
    margin-bottom: 12px;
  }
  .contact__line {
    display: flex; align-items: center; gap: 8px;
    font-size: 15px;
    color: var(--blue-ink);
    line-height: 1.6;
  }
  .contact__line svg { width: 14px; height: 14px; flex: none; }

  /* Back */
  .card--back { left: 490px; top: 480px; }
  .back-field {
    position: absolute; inset: 0;
    background: linear-gradient(135deg, var(--blue-deep) 0%, var(--blue-mid) 50%, var(--blue-light) 100%);
    clip-path: polygon(0 0, 100% 0, 100% 36%, 62% 36%, 62% 58%, 0 58%);
  }
  .back-square {
    position: absolute;
    right: 48px; top: 40px;
    width: 150px; height: 150px;
    background: var(--blue-light);
    border: 6px solid var(--card-white);
    opacity: 0.9;
  }
  .back-brand {
    position: absolute;
    left: 40px; top: 92px;
    font-weight: 700;
    font-size: 40px;
    color: var(--card-white);
    letter-spacing: 0.5px;
    line-height: 1.05;
  }
  .services {
    position: absolute;
    left: 60px; top: 250px;
    list-style: none;
  }
  .services li {
    display: flex; align-items: center; gap: 10px;
    font-size: 17px;
    font-weight: 600;
    color: var(--blue-ink);
    line-height: 1.45;
  }
  .services li::before {
    content: "";
    width: 10px; height: 10px;
    border-radius: 50%;
    background: var(--green);
    flex: none;
  }
</style>
</head>
<body>

  <section class="card card--front" aria-label="Business card front">
    <div class="front-band"></div>
    <div class="brand">
      <span class="brand__name">Summit BladeAir, Inc.</span>
      <span class="brand__mark"></span>
    </div>
    <div class="contact">
      <p class="contact__name">Dennis Tollerby</p>
      <p class="contact__role">Owner</p>
      <p class="contact__line">
        <svg viewBox="0 0 16 16" aria-hidden="true"><path fill="#7cc242" d="M3.6 1.5l2.2 2.6-1.3 1.7c.9 2 2.4 3.5 4.4 4.4l1.7-1.3 2.6 2.2-1.4 2.2C6.6 13.2 2.8 9.4 1.4 2.9z"/></svg>
        626-418-7352
      </p>
      <p class="contact__line">
        <svg viewBox="0 0 16 16" aria-hidden="true"><rect x="1.5" y="3.5" width="13" height="9" fill="none" stroke="#7cc242" stroke-width="1.5"/><path d="M1.5 3.5L8 9l6.5-5.5" fill="none" stroke="#7cc242" stroke-width="1.5"/></svg>
        SummitBladeair@Kestmail.com
      </p>
    </div>
  </section>

  <section class="card card--back" aria-label="Business card back">
    <div class="back-field"></div>
    <div class="back-square"></div>
    <p class="back-brand">Summit<br>BladeAir, Inc.</p>
    <ul class="services">
      <li>Aerial Filming &amp; Photography</li>
      <li>Flight School</li>
      <li>Helicopter Tours (In that order)</li>
    </ul>
  </section>

</body>
</html>
```